Natural healthcare clinic needs stationery and business card design

We have had a logo developed by Pixel Harbor and are now looking at utilising it for a new business concept. The concept is a natural healthcare clinic that hosts a number of small businesses. The individual practitioners may want to utilise the host business stationery to provide a consistent message to clients.

I am looking for a stationery design - letterhead, DL brochure template and business card that uses our logo. The business name 'Bright Meadows' is all about getting rhythm back into your life so you can be fit and healthy. The stationery design should reflect this.

There are a couple of requirements for the business card, it needs to be double-sided with black and white back. There should be lines to write appointment times on. The cards may need to be custom named on the front for example Carol Fenwick, Remedial Therapist and Aromatherapist. Therefore if a template can be provided so we can customise this information using MS Publisher, it would be appreciated.

The DL brochure template needs to be A4 folded to DL. I am looking for a consistent brand message that can be utilised to produce our own clinic brochures.

The natural healthcare clinic will host the following types of businesses - remedial massage, pregnancy massage, oncology massage, aromatherapy, acupuncture - as a bit of a guide.

Target Market(s)

25-45 year old male and females who work full time.

Industry/Entity Type

Healthcare

Requirements
Must have
• Use the logo I have already.

```html
<!DOCTYPE html>
<html lang="en">
<head>
<meta charset="utf-8">
<title>Bright Meadows Letterhead</title>
<link rel="stylesheet" href="https://fonts.googleapis.com/css2?family=Didact+Gothic&family=Open+Sans:wght@400;600&display=swap">
<style>
  :root {
    --backdrop: #ece8e1;
    --paper: #ffffff;
    --olive: #5d6b1f;
    --olive-dark: #1f2a0c;
    --lime: #8dc63f;
    --peach: #f7b98b;
    --ink: #3a3a3a;
    --icon: #e8772e;
    --mist: #f4ece6;
  }
  * { box-sizing: border-box; margin: 0; padding: 0; }
  html, body {
    width: 1200px;
    height: 1024px;
    overflow: hidden;
    background: var(--backdrop);
  }
  .letterhead {
    position: absolute;
    left: 260px;
    top: 31px;
    width: 680px;
    height: 962px;
    background: var(--paper);
    box-shadow: 0 6px 24px rgba(0,0,0,0.18);
    overflow: hidden;
  }
  .brand {
    position: absolute;
    left: 44px;
    top: 56px;
    display: flex;
    align-items: center;
    gap: 12px;
  }
  .brand-dot {
    width: 18px;
    height: 18px;
    border-radius: 50%;
    background: var(--lime);
  }
  .brand-name {
    font-family: "Didact Gothic", sans-serif;
    font-size: 34px;
    color: var(--olive);
    letter-spacing: 0.5px;
  }
  .contact {
    position: absolute;
    right: 40px;
    top: 62px;
    width: 190px;
    font-family: "Open Sans", sans-serif;
    font-style: normal;
    font-weight: 400;
    font-size: 11px;
    line-height: 1.4;
    color: var(--ink);
  }
  .contact p { display: flex; align-items: center; gap: 5px; }
  .contact .address { display: block; margin-bottom: 3px; }
  .contact svg { width: 9px; height: 9px; flex: none; }
  .watermark {
    position: absolute;
    left: 60px;
    top: 230px;
    width: 480px;
    height: 440px;
    border-radius: 50%;
    background: radial-gradient(ellipse at center, var(--mist) 0%, rgba(244,236,230,0) 70%);
  }
  .footer-wave {
    position: absolute;
    left: 0;
    bottom: 0;
    width: 680px;
    height: 230px;
  }
  .website {
    position: absolute;
    left: 40px;
    bottom: 28px;
    font-family: "Open Sans", sans-serif;
    font-size: 12px;
    color: #ffffff;
    letter-spacing: 0.3px;
  }
</style>
</head>
<body>
  <main class="letterhead">
    <header class="brand">
      <span class="brand-dot"></span>
      <span class="brand-name">Bright Meadows</span>
    </header>

    <address class="contact">
      <p class="address">Your address Goes Here, City,<br>Zip code, Country Name</p>
      <p>
        <svg viewBox="0 0 10 10" aria-hidden="true"><path d="M2 1 L4 1 L4.6 3.2 L3.4 4 Q4.4 6 6 6.6 L6.8 5.4 L9 6 L9 8 Q8 9.4 6 8.6 Q2.4 7 1.2 3.6 Q0.8 1.8 2 1 Z" fill="var(--icon)"/></svg>
        555-0142-7730
      </p>
      <p>
        <svg viewBox="0 0 10 10" aria-hidden="true"><rect x="1" y="2" width="8" height="7" rx="1.5" fill="var(--icon)"/><rect x="3" y="1" width="4" height="2" rx="0.6" fill="var(--icon)"/></svg>
        555-0187-2461
      </p>
      <p>
        <svg viewBox="0 0 10 10" aria-hidden="true"><rect x="0.5" y="2" width="9" height="6.5" fill="var(--icon)"/><path d="M0.5 2 L5 5.6 L9.5 2" stroke="#fff" stroke-width="0.8" fill="none"/></svg>
        name@domainname.com
      </p>
    </address>

    <div class="watermark" role="img" aria-label="Faint brand watermark area"></div>

    <svg class="footer-wave" viewBox="0 0 680 230" preserveAspectRatio="none" aria-hidden="true">
      <defs>
        <linearGradient id="bandFill" x1="0" y1="0" x2="1" y2="0">
          <stop offset="0" stop-color="var(--olive-dark)"/>
          <stop offset="0.55" stop-color="#3f5214"/>
          <stop offset="1" stop-color="#6f8d1c"/>
        </linearGradient>
      </defs>
      <path d="M0 40 C180 20 380 140 680 198 L680 230 L0 230 Z" fill="url(#bandFill)"/>
      <path d="M0 30 C180 8 380 128 680 186" stroke="var(--peach)" stroke-width="7" fill="none"/>
      <path d="M170 44 C340 62 480 150 680 172" stroke="var(--lime)" stroke-width="4" fill="none"/>
    </svg>

    <p class="website">www.websitename.com</p>
  </main>
</body>
</html>
```